Bicycle Tour Schedule on a Business Card

Need to develop a 2 side business card that highlights a series of bike tours on 1 side and a series of events on the other side.
This will be inserted into a card wallet that attaches to a cell phone and will be handed out at an expo. The card wallets are black and red so color must coordinate with both. There is a photo of the card wallets attached.

1 side needs to be devoted to Pedal Vista Trek and the others to KQR Venture events on the other. Dates and websites are very important.

Target Market(s)

Cyclists
Predominantly men ages 40+
Educated, Professionals

Industry/Entity Type

Business

Font styles to use
Serif

Requirements
Must have
• Pedal vista treks logo on 1 side and KQR Venture logo on the other side
• dates and websites clearly visible
• Design of both sides must go together.
• Must be portrait not landscape

```html
<!DOCTYPE html>
<html lang="en">
<head>
<meta charset="utf-8">
<title>Pedal Vista Treks &amp; KQR Venture – Event Cards</title>
<link rel="stylesheet" href="https://fonts.googleapis.com/css2?family=PT+Sans:ital,wght@0,400;0,700;1,700&display=swap">
<style>
  :root {
    --backdrop: #8c8d8d;
    --card-white: #f5f5f3;
    --tour-blue: #0f55a0;
    --tour-green: #3fa34d;
    --event-red: #b3132e;
    --event-sky: #2b8fce;
    --on-dark: #ffffff;
  }
  * { margin: 0; padding: 0; box-sizing: border-box; }
  html, body {
    width: 1105px; height: 1200px; overflow: hidden;
    background: var(--backdrop);
    font-family: "PT Sans", "Helvetica Neue", Arial, sans-serif;
  }
  .card {
    position: absolute; top: 269px;
    width: 398px; height: 698px;
    background: var(--card-white);
    overflow: hidden;
    box-shadow: 0 3px 8px rgba(0,0,0,.25);
  }
  .card--tours { left: 113px; }
  .card--events { left: 597px; }
  .wave { position: absolute; left: 0; top: 0; width: 398px; height: 698px; }
  .tagline {
    position: absolute; left: 48px; top: 26px; right: 20px;
    font-style: italic; font-weight: 700; font-size: 20px; line-height: 25px;
  }
  .card--tours .tagline { color: var(--tour-blue); }
  .card--events .tagline { color: var(--event-red); }
  .brand {
    position: absolute; display: flex; align-items: center; gap: 12px;
    font-weight: 700; font-size: 34px; line-height: 1;
  }
  .brand__mark { width: 26px; height: 26px; flex: none; }
  .card--tours .brand { left: 40px; top: 142px; color: var(--tour-green); }
  .card--tours .brand__mark { border-radius: 50%; background: var(--tour-blue); }
  .card--events .brand { left: 48px; top: 120px; color: var(--event-red); }
  .card--events .brand__mark { background: var(--event-red); }
  .schedule {
    position: absolute; right: 38px; list-style: none;
    text-align: right; color: var(--on-dark);
    font-size: 19px; line-height: 23px;
  }
  .card--tours .schedule { top: 384px; }
  .card--tours .schedule li + li { margin-top: 20px; }
  .card--events .schedule { top: 328px; font-size: 18.5px; line-height: 22px; }
  .card--events .schedule li + li { margin-top: 14px; }
  .event__date, .event__web { display: block; font-weight: 700; }
</style>
</head>
<body>

<section class="card card--tours">
  <svg class="wave" viewBox="0 0 398 698" aria-hidden="true">
    <path d="M0,372 C70,398 140,388 200,338 C260,290 320,256 398,252" fill="none" stroke="var(--tour-green)" stroke-width="7"/>
    <path d="M0,382 C70,408 140,398 200,348 C260,300 320,266 398,262 L398,698 L0,698 Z" fill="var(--tour-blue)"/>
  </svg>
  <p class="tagline">Fully supported bike tours.<br>Discover the hidden gems on two wheels</p>
  <div class="brand"><span class="brand__mark"></span>Pedal Vista Treks</div>
  <ul class="schedule">
    <li>Heart of Colorado<span class="event__date">June 26 - July 2, 2016</span></li>
    <li>Colorado Front Range Tour<span class="event__date">August 14-20, 2016</span></li>
    <li>Cape Cod Tour<span class="event__date">October 9 -15, 2016</span></li>
    <li>Florida Key Tours<span class="event__date">November 6-12, 2016 &amp;<br>December 4-10, 2016</span></li>
  </ul>
</section>

<section class="card card--events">
  <svg class="wave" viewBox="0 0 398 698" aria-hidden="true">
    <path d="M0,308 C50,338 100,346 170,318 C250,284 320,214 398,200" fill="none" stroke="var(--event-sky)" stroke-width="7"/>
    <path d="M0,318 C50,348 100,356 170,328 C250,294 320,224 398,210 L398,698 L0,698 Z" fill="var(--event-red)"/>
  </svg>
  <p class="tagline">Tri Spoke Series:<br>Cycling camps for youth</p>
  <div class="brand"><span class="brand__mark"></span>KQR Venture</div>
  <ul class="schedule">
    <li>Mountain Bike Camp<span class="event__date">July 8-10, 2016</span></li>
    <li>Cyclocross Camp<span class="event__date">August 26-28, 2016</span><span class="event__web">Trispokeseries.org</span></li>
    <li>Mile High Century Ride<span class="event__date">June 18, 2016</span><span class="event__web">Milehighcenturyride.com</span></li>
    <li>Colorado Peak 2 Peak Challenge<span class="event__date">July 30, 2016 - Copeak2peak.com</span></li>
    <li>Zany Bike Ride<span class="event__date">September 11, 2016</span><span class="event__web">zanybikeride.com</span></li>
  </ul>
</section>

</body>
</html>
```